Birchpoint Studio Complementary Pass

I’d like a complimentary pass for any 30-minute Birchpoint Studio session. Choose one of the following options: Infrared Sauna with Red Light, Massage Chair Veltrafix Compression Therapy, or Paraffin Wax Hand Bath.

Please incorporate the logo and brand colors into your design. I’d like a square image that will be printed on square business cards (no rectangles).

Please refer to the logo and menu for more details.

Contact Information for Business Card

See discretion

```html
<!DOCTYPE html>
<html lang="en">
<head>
<meta charset="UTF-8">
<title>Birchpoint Studio Complimentary Pass</title>
<link rel="stylesheet" href="https://fonts.googleapis.com/css2?family=Montserrat:wght@400;500;700;800&family=Kaushan+Script&display=swap">
<style>
  :root{
    --bg:#0d0d0d;
    --orange:#f0643f;
    --orange-soft:#f27a55;
    --purple:#473494;
    --purple-deep:#3d2b86;
    --white:#ffffff;
    --ink:#3a2d86;
  }
  *{box-sizing:border-box;margin:0;padding:0}
  html,body{width:1200px;height:800px;overflow:hidden;background:var(--bg)}
  body{font-family:"Montserrat",Arial,sans-serif;position:relative}

  .card{
    position:absolute;top:150px;width:500px;height:500px;
    border-radius:36px;overflow:hidden;
    box-shadow:0 18px 40px rgba(0,0,0,.55);
  }

  /* Front */
  .card--front{
    left:70px;
    background:linear-gradient(160deg,var(--orange) 0%,#c2506b 35%,#6a3a92 65%,var(--purple) 100%);
    display:flex;flex-direction:column;align-items:center;justify-content:center;gap:14px;
  }
  .front-mark{display:flex;align-items:center;gap:16px}
  .front-mark__dot{width:26px;height:26px;border-radius:50%;background:var(--white)}
  .front-name{font-weight:700;font-size:86px;color:var(--white);letter-spacing:1px;line-height:1}
  .front-tag{font-weight:700;font-size:27px;color:var(--white);letter-spacing:6px;text-transform:uppercase}

  /* Back */
  .card--back{left:630px;background:var(--white)}
  .back-wave{position:absolute;left:0;bottom:0;width:500px;height:240px}
  .back-top{position:absolute;left:0;right:0;top:0;text-align:center}
  .brand{margin-top:30px;display:flex;flex-direction:column;align-items:center}
  .brand__name{font-weight:700;font-size:34px;color:var(--purple);line-height:1}
  .brand__tag{font-weight:500;font-size:10px;color:var(--purple);letter-spacing:3px;text-transform:uppercase;margin-top:4px}

  .title-row{display:flex;align-items:center;justify-content:center;gap:12px;margin-top:14px}
  .title-row__rule{width:60px;height:1.5px;background:var(--purple)}
  .title-script{font-family:"Kaushan Script",cursive;font-size:36px;color:var(--purple);line-height:1.1}

  .pass-title{font-weight:800;font-size:30px;color:var(--orange);letter-spacing:.5px;margin-top:6px}
  .offer{font-size:15px;color:var(--ink);margin-top:8px;line-height:1.4}
  .offer__hl{color:var(--orange)}
  .offer__choose{color:var(--orange);font-weight:800}

  .options{position:absolute;left:20px;right:20px;top:262px;display:flex;justify-content:space-between;align-items:flex-start}
  .option{border:2px solid var(--orange);border-radius:8px;padding:7px 10px;font-size:13.5px;line-height:1.25;text-align:center;color:var(--ink);background:var(--white)}
  .option--lower{margin-top:40px}
  .option--mid{margin-top:18px;border-color:var(--purple)}
  .option--mid .option__lead{color:var(--orange)}

  .contact{position:absolute;left:28px;bottom:26px;color:var(--white);font-size:11.5px;line-height:1.55}
  .contact__row{display:flex;align-items:flex-start;gap:8px}
  .contact__icon{width:12px;height:12px;flex:none;margin-top:2px}
  .note{position:absolute;right:24px;bottom:70px;width:210px;color:var(--white);font-size:10px;line-height:1.4;text-align:right}
</style>
</head>
<body>

  <section class="card card--front" aria-label="Pass front">
    <div class="front-mark">
      <span class="front-mark__dot"></span>
      <span class="front-name">Solvia</span>
    </div>
    <p class="front-tag">Physical Therapy</p>
  </section>

  <section class="card card--back" aria-label="Pass back">
    <svg class="back-wave" viewBox="0 0 500 240" preserveAspectRatio="none" aria-hidden="true">
      <path d="M0 110 C120 40 260 110 380 70 C440 50 480 20 500 0 L500 240 L0 240 Z" fill="var(--purple)"/>
      <path d="M0 110 C120 40 260 110 380 70 C440 50 480 20 500 0 L500 14 C470 44 430 68 380 82 C260 118 120 56 0 124 Z" fill="var(--orange)"/>
      <path d="M0 98 C120 30 260 100 380 60 C440 40 478 14 500 -4" fill="none" stroke="var(--purple)" stroke-width="3"/>
    </svg>

    <div class="back-top">
      <div class="brand">
        <span class="brand__name">Solvia</span>
        <span class="brand__tag">Physical Therapy</span>
      </div>
      <div class="title-row">
        <span class="title-row__rule"></span>
        <h1 class="title-script">Birchpoint Studio</h1>
        <span class="title-row__rule"></span>
      </div>
      <h2 class="pass-title">COMPLIMENTARY PASS</h2>
      <p class="offer">Any <span class="offer__hl">30-Minute</span> Birchpoint Studio Session.<br>on us! <span class="offer__choose">Choose one:</span></p>
    </div>

    <div class="options">
      <div class="option option--lower">Infrared Sauna<br>+ Red Light</div>
      <div class="option option--mid"><span class="option__lead">Massage Chair Veltrafix</span><br>Compression Therapy</div>
      <div class="option">Paraffin Wax<br>Hand Bath</div>
    </div>

    <div class="contact">
      <div class="contact__row">
        <svg class="contact__icon" viewBox="0 0 12 12" aria-hidden="true"><path d="M6 0.5a4 4 0 0 1 4 4c0 3-4 7-4 7s-4-4-4-7a4 4 0 0 1 4-4z" fill="none" stroke="#fff" stroke-width="1.2"/><circle cx="6" cy="4.5" r="1.4" fill="#fff"/></svg>
        <span>Street, Apartment, City, State,<br>Post Code, Country</span>
      </div>
      <div class="contact__row">
        <svg class="contact__icon" viewBox="0 0 12 12" aria-hidden="true"><path d="M2.5 1l2 2.2-1 1.3a7 7 0 0 0 4 4l1.3-1 2.2 2-1.2 1.5C5.5 11 1 6.5 1 2.2z" fill="#fff"/></svg>
        <span>(555) 214-0387</span>
      </div>
      <div class="contact__row">
        <svg class="contact__icon" viewBox="0 0 12 12" aria-hidden="true"><circle cx="6" cy="6" r="5" fill="none" stroke="#fff" stroke-width="1.2"/><path d="M1 6h10M6 1c2 2.5 2 7.5 0 10M6 1c-2 2.5-2 7.5 0 10" fill="none" stroke="#fff" stroke-width="1"/></svg>
        <span>www.solviapt.com</span>
      </div>
      <div class="contact__row">
        <svg class="contact__icon" viewBox="0 0 12 12" aria-hidden="true"><rect x="0.8" y="2.5" width="10.4" height="7.5" rx="1" fill="none" stroke="#fff" stroke-width="1.2"/><path d="M1 3l5 4 5-4" fill="none" stroke="#fff" stroke-width="1.2"/></svg>
        <span>info@solviapt.com</span>
      </div>
    </div>

    <p class="note">*For safety, a rest/cool-down period is required after 30 minutes in the sauna.</p>
  </section>

</body>
</html>
```